SaaS Early tech startup business card design

Unique design for experience ecommerce platform company. the business cards will be used by executive members. conformance with color code is required.

```html
<!DOCTYPE html>
<html lang="en">
<head>
<meta charset="utf-8">
<title>nuvo business card</title>
<link rel="stylesheet" href="https://fonts.googleapis.com/css2?family=Roboto:wght@400;500;700;900&display=swap">
<style>
  :root {
    --page: #d9dadb;
    --card-white: #ffffff;
    --brand-blue: #0b5f8f;
    --brand-deep: #0a5a8c;
    --brand-teal: #14a88e;
    --brand-sea: #0e8a8f;
    --ink: #3d3d3d;
  }
  * { box-sizing: border-box; margin: 0; padding: 0; }
  html, body { width: 1200px; height: 800px; overflow: hidden; }
  body {
    background: var(--page);
    font-family: "Roboto", Arial, sans-serif;
    position: relative;
  }
  .card {
    position: absolute;
    top: 245px;
    width: 540px;
    height: 309px;
    box-shadow: 0 10px 28px rgba(0,0,0,0.18);
    overflow: hidden;
  }
  .card--front { left: 40px; background: var(--card-white); }
  .card--back {
    left: 620px;
    background: linear-gradient(150deg, var(--brand-sea) 0%, #0c7f94 45%, var(--brand-deep) 100%);
  }
  .edge-band {
    position: absolute;
    left: 0; top: 0; bottom: 0;
    width: 20px;
    background: linear-gradient(180deg, var(--brand-deep) 0%, #1191a0 25%, var(--brand-teal) 45%, #0c6f96 65%, var(--brand-teal) 82%, var(--brand-deep) 100%);
  }
  .contact {
    position: absolute;
    left: 62px;
    top: 78px;
  }
  .contact__name {
    font-weight: 700;
    font-size: 21px;
    color: var(--brand-blue);
    letter-spacing: 0.2px;
    line-height: 1;
  }
  .contact__title {
    font-weight: 500;
    font-size: 14px;
    color: var(--brand-teal);
    margin-top: 3px;
  }
  .contact__address {
    font-size: 13px;
    color: var(--ink);
    line-height: 1.3;
    margin-top: 14px;
  }
  .contact__list {
    list-style: none;
    margin-top: 12px;
  }
  .contact__list li {
    display: flex;
    align-items: center;
    gap: 10px;
    font-size: 13px;
    color: var(--ink);
    line-height: 1.35;
  }
  .contact__list svg { width: 11px; height: 11px; flex: none; }
  .wordmark {
    position: absolute;
    font-weight: 900;
    letter-spacing: -1px;
    line-height: 1;
  }
  .card--front .wordmark {
    right: 60px;
    top: 118px;
    font-size: 64px;
    color: var(--brand-blue);
  }
  .card--back .wordmark {
    right: 46px;
    bottom: 44px;
    font-size: 62px;
    color: var(--card-white);
  }
  .back-pattern {
    position: absolute;
    inset: 0;
    background: linear-gradient(160deg, rgba(20,168,142,0.25) 0%, rgba(10,90,140,0.25) 100%);
  }
</style>
</head>
<body>
  <section class="card card--front">
    <div class="edge-band" role="img" aria-label="Decorative band of blue and teal squares"></div>
    <div class="contact">
      <h1 class="contact__name">DANIEL REYES</h1>
      <p class="contact__title">President</p>
      <p class="contact__address">2140 Willow Creek Road<br>Fairbanks, Alaska 99701</p>
      <ul class="contact__list">
        <li><svg viewBox="0 0 12 12"><path d="M2 1h3l1 3-1.5 1a6 6 0 0 0 2.5 2.5L8 6l3 1v3c-5 1-10-4-9-9z" fill="#14a88e"/></svg>555-204-7731</li>
        <li><svg viewBox="0 0 12 12"><rect x="3" y="0.5" width="6" height="11" rx="1" fill="none" stroke="#14a88e" stroke-width="1.3"/></svg>555-318-4406</li>
        <li><svg viewBox="0 0 12 12"><rect x="1" y="4" width="10" height="7" rx="1" fill="#14a88e"/><rect x="3" y="1" width="6" height="3" fill="none" stroke="#14a88e" stroke-width="1.2"/></svg>555-462-9180</li>
        <li><svg viewBox="0 0 12 12"><rect x="0.5" y="2" width="11" height="8" rx="1" fill="#14a88e"/><path d="M1 3l5 4 5-4" fill="none" stroke="#fff" stroke-width="1.1"/></svg>hello@nuvo.com</li>
        <li><svg viewBox="0 0 12 12"><circle cx="6" cy="6" r="5.5" fill="#14a88e"/><path d="M0.5 6h11M6 0.5c-3 3-3 8 0 11M6 0.5c3 3 3 8 0 11" fill="none" stroke="#fff" stroke-width="0.9"/></svg>www.nuvo.com</li>
      </ul>
    </div>
    <div class="wordmark">nuvo</div>
  </section>

  <section class="card card--back">
    <div class="back-pattern" role="img" aria-label="Checkered pattern of teal and blue squares"></div>
    <div class="wordmark">nuvo</div>
  </section>
</body>
</html>
```